Corvane Capital Business Cards

These are professional business cards that are for my family office.
Put fake emails and phone numbers as of now until I finalize those components. This family office controls my families investments, assets, and future. The cards should be professional.
..
.
.
.
I just uploaded another variation of a logo I would like to see as a business card to I am inbeteen which logo to use

Target Market(s)

business

Industry/Entity Type

business

Contact Information for Business Card

Professional, wealth related, finance related.

Requirements
Must have
• Logo

```html
<!DOCTYPE html>
<html lang="en">
<head>
<meta charset="utf-8">
<title>Corvane Capital Business Cards</title>
<link rel="stylesheet" href="https://fonts.googleapis.com/css2?family=Cinzel:wght@600;700&family=Arimo:wght@400&display=swap">
<style>
  :root {
    --backdrop: #3d3d3d;
    --navy: #1b1f2d;
    --paper: #ffffff;
    --ink: #1b1f2d;
    --on-navy: #f2f3f5;
    --rule: #8a8e99;
  }
  * { margin: 0; padding: 0; box-sizing: border-box; }
  html, body {
    width: 1200px; height: 803px; overflow: hidden;
    background: var(--backdrop);
  }
  .stage {
    width: 1200px; height: 803px;
    display: flex; align-items: center; justify-content: center; gap: 60px;
  }
  .card {
    width: 500px; height: 286px;
    border-radius: 18px;
    position: relative;
    overflow: hidden;
  }
  .card-back {
    background: var(--navy);
    color: var(--on-navy);
    display: flex; align-items: center; justify-content: center;
  }
  .identity {
    text-align: right;
    padding-right: 16px;
    font-family: "Arimo", Arial, sans-serif;
    font-size: 12.5px;
    line-height: 1.35;
  }
  .identity .person {
    font-family: "Cinzel", "Times New Roman", serif;
    font-weight: 700;
    font-size: 21px;
    letter-spacing: 0.5px;
    line-height: 1.1;
    margin-bottom: 2px;
  }
  .divider {
    width: 1px; height: 76px;
    background: var(--rule);
  }
  .contacts {
    list-style: none;
    padding-left: 12px;
    font-family: "Arimo", Arial, sans-serif;
    font-size: 12.5px;
    line-height: 1.45;
  }
  .contacts li { display: flex; align-items: center; gap: 7px; }
  .contacts svg { width: 11px; height: 11px; flex: none; }
  .card-front {
    background: var(--paper);
    color: var(--ink);
    display: flex; flex-direction: column; align-items: center; justify-content: center;
    gap: 22px;
  }
  .brand-dot {
    width: 96px; height: 96px;
    border: 3px solid var(--ink);
    border-radius: 50%;
  }
  .brand-name {
    font-family: "Cinzel", "Times New Roman", serif;
    font-weight: 600;
    font-size: 30px;
    letter-spacing: 1.5px;
    color: var(--ink);
  }
</style>
</head>
<body>
<main class="stage">
  <section class="card card-back" aria-label="Card back with contact details">
    <div class="identity">
      <p class="person">Daniel Hart</p>
      <p class="role">President</p>
      <p class="address">412 Linden Court</p>
      <p class="address">Halden, Canada 20981</p>
    </div>
    <div class="divider"></div>
    <ul class="contacts">
      <li>
        <svg viewBox="0 0 12 12" aria-hidden="true"><path d="M3 1l2 2.5-1.2 1.3c.6 1.3 1.6 2.3 2.9 2.9L8 6.5 10.5 8.5 9.5 10.5C5.5 10.5 1.5 6.5 1.5 2.5z" fill="currentColor"/></svg>
        555-201-4830
      </li>
      <li>
        <svg viewBox="0 0 12 12" aria-hidden="true"><rect x="1.5" y="2" width="9" height="8" rx="0.8" fill="none" stroke="currentColor" stroke-width="1.2"/></svg>
        555-201-4876
      </li>
      <li>
        <svg viewBox="0 0 12 12" aria-hidden="true"><rect x="1" y="2.5" width="10" height="7" fill="currentColor"/><path d="M1 2.5l5 4 5-4" fill="none" stroke="#1b1f2d" stroke-width="1"/></svg>
        info@corvanecapital.com
      </li>
      <li>
        <svg viewBox="0 0 12 12" aria-hidden="true"><circle cx="6" cy="6" r="5" fill="currentColor"/><path d="M1 6h10M6 1c2 2.5 2 7.5 0 10M6 1c-2 2.5-2 7.5 0 10" fill="none" stroke="#1b1f2d" stroke-width="0.8"/></svg>
        www.corvanecapital.com
      </li>
    </ul>
  </section>

  <section class="card card-front" aria-label="Card front with company name">
    <div class="brand-dot" aria-hidden="true"></div>
    <p class="brand-name">Corvane Capital</p>
  </section>
</main>
</body>
</html>
```